Accounting firm needing business card / letterhead designed
Marcus L. Trenholm, CPA
marcus@veltrowledger.com
www.veltrowledger.com
842 E Alder Ave Perrysburg, OH 43827
419-562-0974

```html
<!DOCTYPE html>
<html lang="en">
<head>
<meta charset="utf-8">
<title>Veltrow Ledger Business Card</title>
<link rel="stylesheet" href="https://fonts.googleapis.com/css2?family=Michroma&family=Roboto:wght@400&display=swap">
<style>
  :root {
    --navy: #272262;
    --navy-light: #443a9e;
    --green: #8cc63f;
    --paper: #f6f6f6;
    --paper-edge: #e8e8e8;
    --ink: #4a4a4a;
    --backdrop: #1b1b1b;
  }
  html, body {
    margin: 0;
    width: 1200px;
    height: 960px;
    overflow: hidden;
    background: var(--backdrop);
  }
  .stage { position: relative; width: 1200px; height: 960px; }

  .card {
    position: absolute;
    width: 600px;
    height: 342px;
    overflow: hidden;
  }
  .card-front {
    left: 302px; top: 129px;
    background: linear-gradient(135deg, #fafafa 0%, var(--paper) 45%, var(--paper-edge) 100%);
  }
  .card-back {
    left: 299px; top: 488px;
    background: linear-gradient(150deg, var(--navy-light) 0%, #312a7d 25%, var(--navy) 55%, var(--navy) 100%);
  }

  .brand-name {
    font-family: "Michroma", sans-serif;
    font-weight: 400;
    margin: 0;
    white-space: nowrap;
    line-height: 1;
  }
  .card-front .brand-name {
    position: absolute;
    left: 34px; top: 72px;
    font-size: 24px;
    letter-spacing: 1px;
    color: var(--navy);
  }
  .card-back .brand-name {
    position: absolute;
    left: 0; right: 0; top: 156px;
    text-align: center;
    font-size: 26px;
    letter-spacing: 1.5px;
    color: #ffffff;
  }

  .contact {
    position: absolute;
    left: 33px; top: 214px;
    font-family: "Roboto", sans-serif;
    font-style: normal;
    font-size: 14px;
    line-height: 18px;
    color: var(--ink);
  }
  .contact .address { margin: 0 0 3px; }
  .contact .line { display: flex; align-items: center; gap: 8px; margin: 0; height: 19px; }
  .contact svg { width: 13px; height: 13px; fill: var(--navy); flex: none; }

  .holder-name {
    position: absolute;
    right: 34px; top: 249px;
    font-family: "Michroma", sans-serif;
    font-size: 13px;
    line-height: 1;
    letter-spacing: 0.4px;
    color: var(--navy);
    margin: 0;
    white-space: nowrap;
  }

  .footer-band { position: absolute; left: 0; top: 300px; width: 600px; height: 42px; }
  .website {
    position: absolute;
    right: 28px; top: 318px;
    font-family: "Roboto", sans-serif;
    font-size: 13px;
    line-height: 16px;
    letter-spacing: 2px;
    color: var(--green);
    margin: 0;
  }
</style>
</head>
<body>
<main class="stage">
  <section class="card card-front">
    <h1 class="brand-name">VELTROW LEDGER</h1>

    <address class="contact">
      <p class="address">842 E Alder Ave<br>Perrysburg, OH 43827</p>
      <p class="line">
        <svg viewBox="0 0 24 24" aria-hidden="true"><path d="M6.6 10.8a15.1 15.1 0 0 0 6.6 6.6l2.2-2.2c.3-.3.7-.4 1-.2 1.1.4 2.3.6 3.6.6.6 0 1 .4 1 1V20c0 .6-.4 1-1 1A17 17 0 0 1 3 4c0-.6.4-1 1-1h3.5c.6 0 1 .4 1 1 0 1.3.2 2.5.6 3.6.1.3 0 .7-.2 1z"/></svg>
        419-562-0974
      </p>
      <p class="line">
        <svg viewBox="0 0 24 24" aria-hidden="true"><rect x="2" y="5" width="20" height="14"/><path d="M3 6l9 7 9-7v1.4l-9 7-9-7z" fill="#fff"/></svg>
        marcus@veltrowledger.com
      </p>
    </address>

    <p class="holder-name">MARCUS L. TRENHOLM, CPA</p>

    <svg class="footer-band" viewBox="0 0 600 42" aria-hidden="true">
      <rect x="0" y="34" width="600" height="8" fill="var(--navy)"/>
      <polygon points="350,42 374,11 587,11 587,42" fill="var(--navy)"/>
      <rect x="589" y="11" width="11" height="31" fill="var(--green)"/>
    </svg>
    <p class="website">www.veltrowledger.com</p>
  </section>

  <section class="card card-back">
    <h2 class="brand-name">VELTROW LEDGER</h2>
  </section>
</main>
</body>
</html>
```